Bright Harbor Counseling Letterhead for hip modern business

I would like some ombre use of the colors in the logo hip letterhead that incorporates logo colors and feel, needs to connect with young professionals and college students. i need to be able to write letters to schools to excuse absences as well. i like color blocks on one side preferably using colors from the attached logo design.

Target Market(s)

high income young people, young adults and college students

Industry/Entity Type

mental health

Font styles to use
Serif
Sans Serif

Colors
0054AA
0677BA
7BADD7
CADEEF
E8F1F8
0094D4
00A9DD
6FCCEA
C7EBF8
E9F6FB
00AB8E
00BBA5
67D7C9
C6EFE9
E9F9F6
59FF00
82FF00
B8FF75
E3FFCB
F4FFEA
A7469A
B969AE
D3A5CF
EDDBEB
F8F0F9
6B429C
8869AF
B7A5CE
E3DAEB
F3F0F8

Requirements
Must have
• a modern hip feel, somewhat color

```html
<!DOCTYPE html>
<html lang="en">
<head>
<meta charset="utf-8">
<title>Bright Harbor Counseling – Letterhead and Envelope</title>
<link href="https://fonts.googleapis.com/css2?family=Open+Sans:wght@300;400;600&display=swap" rel="stylesheet">
<style>
  :root {
    --bg: #e9e9eb;
    --paper: #fbfbfb;
    --ink: #3a3a3c;
    --ink-soft: #5a5a5e;
    --brand-grey: #4a4a4e;
    --black: #1c1c1e;
    --blue: #0677ba;
    --purple: #8f3f8a;
    --teal: #4fbfae;
    --accent-dot: #8869af;
    --flap-line: #dcdcde;
    --white: #ffffff;
  }
  * { margin: 0; padding: 0; box-sizing: border-box; }
  html, body { width: 1200px; height: 795px; overflow: hidden; }
  body {
    background: var(--bg);
    font-family: "Open Sans", Arial, sans-serif;
    color: var(--ink);
    position: relative;
  }

  /* Letterhead sheet */
  .letterhead {
    position: absolute;
    left: 60px; top: 30px;
    width: 520px; height: 735px;
    background: var(--paper);
    box-shadow: 0 2px 10px rgba(0,0,0,0.12);
    overflow: hidden;
  }
  .brand {
    position: absolute;
    display: flex; align-items: center; gap: 10px;
  }
  .brand-name {
    font-weight: 300;
    color: var(--brand-grey);
    line-height: 1.05;
  }
  .brand-dot {
    border-radius: 50%;
    background: var(--accent-dot);
    flex: none;
  }
  .letterhead .brand { right: 40px; top: 40px; }
  .letterhead .brand-name { font-size: 20px; text-align: right; }
  .letterhead .brand-dot { width: 30px; height: 30px; }

  .contact {
    position: absolute;
    right: 40px; top: 112px;
    font-size: 8.5px;
    line-height: 1.55;
    color: var(--ink-soft);
    list-style: none;
  }
  .contact li { display: flex; align-items: center; gap: 5px; }
  .contact svg { width: 8px; height: 8px; fill: var(--blue); flex: none; }
  .contact .address { padding-left: 13px; }

  .letter {
    position: absolute;
    left: 48px; top: 185px;
    width: 424px;
    font-size: 8.6px;
    line-height: 1.5;
    color: var(--ink);
  }
  .letter .salutation { margin-bottom: 12px; }
  .letter p.body { margin-bottom: 12px; padding-left: 14px; }
  .letter .closing { margin-top: 4px; }
  .signature {
    display: block;
    margin-top: 14px;
    width: 90px; height: 40px;
    border-radius: 4px;
    background: linear-gradient(90deg, #ececee, #e2e2e4);
  }

  .footer-band {
    position: absolute;
    left: 0; bottom: 0;
    width: 520px; height: 40px;
    display: block;
  }
  .footer-url {
    font-family: "Open Sans", Arial, sans-serif;
    font-size: 11.5px;
    font-weight: 600;
    fill: var(--white);
  }

  /* Envelope */
  .envelope {
    position: absolute;
    left: 630px; top: 260px;
    width: 520px; height: 260px;
    background: var(--paper);
    box-shadow: 0 2px 10px rgba(0,0,0,0.12);
  }
  .envelope .flap { position: absolute; inset: 0; width: 100%; height: 100%; }
  .envelope .brand { right: 48px; top: 128px; }
  .envelope .brand-name { font-size: 19px; text-align: right; }
  .envelope .brand-dot { width: 28px; height: 28px; }
</style>
</head>
<body>

<section class="letterhead" aria-label="Letterhead">
  <div class="brand">
    <span class="brand-name">Bright Harbor<br>Counseling</span>
    <span class="brand-dot"></span>
  </div>

  <ul class="contact">
    <li class="address">48 Lakeview Crescent,</li>
    <li class="address">Maple Glen, ON L7K 3R5</li>
    <li><svg viewBox="0 0 10 10"><path d="M2 0h2l1 3-1.5 1a6 6 0 0 0 2.5 2.5L7 5l3 1v2a2 2 0 0 1-2 2A8 8 0 0 1 0 2a2 2 0 0 1 2-2z"/></svg>(555) 302-4417</li>
    <li><svg viewBox="0 0 10 10"><rect x="1" y="3" width="8" height="6" rx="1"/><rect x="3" y="0" width="4" height="3"/></svg>(555) 618-2290</li>
    <li><svg viewBox="0 0 10 10"><path d="M0 2h10v6H0z M0 2l5 3.5L10 2" /></svg>hello@brightharbor.com</li>
  </ul>

  <div class="letter">
    <p class="salutation">Dear customer,</p>
    <p class="body">Lorem ipsum dolor sit amet, consectetur adipisicing elit, sed do eiusmod tempor incididunt ut labore et dolore magna aliqua. Ut enim ad minim veniam, quis nostrud exercitation ullamco laboris nisi ut aliquip ex ea commodo consequat. Duis aute irure dolor in reprehenderit in voluptate velit esse cillum dolore eu fugiat nulla pariatur. Excepteur sint occaecat cupidatat non proident, sunt in culpa qui officia deserunt mollit anim id est laborum.</p>
    <p class="body">Lorem ipsum dolor sit amet, consectetur adipisicing elit, sed do eiusmod tempor incididunt ut labore et dolore magna aliqua. Ut enim ad minim veniam, quis nostrud exercitation ullamco laboris nisi ut aliquip ex ea commodo consequat. Duis aute irure dolor in reprehenderit in voluptate velit esse cillum dolore eu fugiat nulla pariatur. Excepteur sint occaecat cupidatat non proident, sunt in culpa qui officia deserunt mollit anim id est laborum.</p>
    <p class="body">Lorem ipsum dolor sit amet, consectetur adipisicing elit, sed do eiusmod tempor incididunt ut labore et dolore magna aliqua. Ut enim ad minim veniam, quis nostrud exercitation ullamco laboris nisi ut aliquip ex ea commodo consequat. Duis aute irure dolor in reprehenderit in voluptate velit esse cillum dolore eu fugiat nulla pariatur. Excepteur sint occaecat cupidatat non proident, sunt in culpa qui officia deserunt mollit anim id est laborum.</p>
    <p class="body">Lorem ipsum dolor sit amet, consectetur adipisicing elit, sed do eiusmod tempor incididunt ut labore et dolore magna aliqua. Ut enim ad minim veniam, quis nostrud exercitation ullamco laboris nisi ut aliquip ex ea commodo consequat. Duis aute irure dolor.</p>
    <p class="closing">Yours Sincerely,</p>
    <span class="signature" role="img" aria-label="Handwritten signature"></span>
  </div>

  <svg class="footer-band" viewBox="0 0 520 40" role="presentation">
    <path d="M0 33 H336 C350 33 350 12 368 12 H520 V40 H0 Z" fill="var(--black)"/>
    <rect x="0" y="28" width="108" height="5" fill="var(--blue)"/>
    <rect x="112" y="28" width="108" height="5" fill="var(--purple)"/>
    <rect x="224" y="28" width="108" height="5" fill="var(--teal)"/>
    <text class="footer-url" x="504" y="30" text-anchor="end">www.brightharbor.com</text>
  </svg>
</section>

<section class="envelope" aria-label="Envelope">
  <svg class="flap" viewBox="0 0 520 260" preserveAspectRatio="none" aria-hidden="true">
    <path d="M10 6 H510 L500 60 H20 Z" fill="none" stroke="var(--flap-line)" stroke-width="1.2" stroke-linejoin="round"/>
  </svg>
  <div class="brand">
    <span class="brand-name">Bright Harbor<br>Counseling</span>
    <span class="brand-dot"></span>
  </div>
</section>

</body>
</html>
```